A new presentation to our clients

we are a Real Estate agency, our website is www.lumibrasa.com and it’s time to have a new, fashion and remarcable Business Card. we want to differentiate ourselves from other companies so we want a business card that differentiates us. we want the business card to impact our customers. in the competitive market that we have today, we have to be different and it is this difference that we seek

Target Market(s)

Real Estate Clients

Contact Information for Business Card

We search a totaly diferent card from the usual

Font styles to use
Sans Serif

Colors
e34197

Requirements
Must have
• Logo, adress, phone contact, e-mail, photo, and our website
Nice to have
• We would like to see a modern business card
Should not have
• Houses or building draws

```html
<!DOCTYPE html>
<html lang="pt">
<head>
<meta charset="utf-8">
<title>Lumi Brasa — Business Card</title>
<link rel="stylesheet" href="https://fonts.googleapis.com/css2?family=Work+Sans:wght@400;500;600&display=swap">
<style>
  :root {
    --stage: #2a2a2c;
    --brand: #e0196f;
    --brand-deep: #a3124f;
    --paper: #ffffff;
    --paper-shade: #ececec;
    --ink: #4a4a4a;
    --logo-light: #d9d9d9;
  }
  * { box-sizing: border-box; margin: 0; padding: 0; }
  html, body { width: 1200px; height: 900px; overflow: hidden; }
  body {
    background: var(--stage);
    font-family: "Work Sans", Arial, sans-serif;
    display: flex;
    align-items: center;
    justify-content: center;
    gap: 50px;
  }
  .card {
    width: 525px;
    height: 300px;
    border-radius: 16px;
    position: relative;
    overflow: hidden;
    box-shadow: 0 10px 30px rgba(0,0,0,0.45);
  }

  /* Front side */
  .card-front {
    background: linear-gradient(135deg, var(--paper-shade) 0%, var(--paper) 45%, var(--paper) 100%);
  }
  .brand-name {
    position: absolute;
    left: 36px;
    top: 30px;
    font-size: 40px;
    font-weight: 500;
    color: var(--brand);
    letter-spacing: 0.5px;
  }
  .contact-list {
    position: absolute;
    left: 36px;
    top: 104px;
    display: grid;
    grid-template-columns: 52px 14px auto;
    row-gap: 3px;
    font-size: 13px;
    line-height: 1.25;
  }
  .contact-label { color: var(--brand); }
  .contact-sep { color: var(--brand); }
  .contact-value { color: var(--ink); }
  .address {
    position: absolute;
    left: 36px;
    bottom: 34px;
    font-size: 13px;
    line-height: 1.45;
    color: var(--ink);
  }
  .person {
    position: absolute;
    right: 46px;
    bottom: 70px;
    text-align: right;
  }
  .person-name {
    font-size: 24px;
    font-weight: 500;
    color: var(--brand);
    letter-spacing: 0.3px;
    text-transform: uppercase;
  }
  .person-role {
    font-size: 13px;
    color: var(--ink);
    margin-top: 2px;
  }
  .accent-tab {
    position: absolute;
    right: 0;
    bottom: 74px;
    width: 30px;
    height: 38px;
    background: var(--brand);
  }

  /* Back side */
  .card-back {
    background: linear-gradient(135deg, var(--brand) 0%, var(--brand-deep) 100%);
    display: flex;
    align-items: center;
    justify-content: center;
  }
  .brand-name-large {
    font-size: 62px;
    font-weight: 500;
    color: var(--logo-light);
    letter-spacing: 1px;
  }
</style>
</head>
<body>
  <section class="card card-front" aria-label="Business card front">
    <div class="brand-name">Lumi Brasa</div>

    <div class="contact-list">
      <span class="contact-label">Phone</span><span class="contact-sep">:</span><span class="contact-value">(+351) 220 555 140</span>
      <span class="contact-label">Fax</span><span class="contact-sep">:</span><span class="contact-value">(+351) 220 555 149</span>
      <span class="contact-label">Email</span><span class="contact-sep">:</span><span class="contact-value">geral@lumibrasa.com</span>
      <span class="contact-label">Web</span><span class="contact-sep">:</span><span class="contact-value">www.lumibrasa.com</span>
    </div>

    <div class="address">
      Rua do Sol Nascente, 118<br>
      4400-512, Vila Serena
    </div>

    <div class="person">
      <div class="person-name">Daniel Moreira</div>
      <div class="person-role">Director</div>
    </div>
    <div class="accent-tab"></div>
  </section>

  <section class="card card-back" aria-label="Business card back">
    <div class="brand-name-large">Lumi Brasa</div>
  </section>
</body>
</html>
```